Commercial Refrigeration Service Company requires stylish and fresh looking flyer.

We need a flyer to hand out to new customers. It should have a photo and our branding, list all the services that are offered and our contact details.
We would like two flyers to be supplied, both identical though one offering a discount until July ( Half Price Service Fee ). The flyer should be clear, interesting and in similar colours to the branding package supplied.
Please look at our website for information about the services on offer:
www.brisko-coolworks.com.au

Target Market(s)

Cafes, bars, restaurants, pubs ect.

Font styles to use
Other font styles liked:
• Font package provided

Colors
85cae6
ffffff
333333

Requirements
Must have
• - The photo provided.
• - The company logo.
• - Similar feel to the website & business card.
• - Smooth layout and clear to understand.
Should not have
• - No clunky badges or prints.

```html
<!DOCTYPE html>
<html lang="en">
<head>
<meta charset="utf-8">
<title>Brisko Commercial Refrigeration Flyer</title>
<link href="https://fonts.googleapis.com/css2?family=Raleway:wght@300;400;500&family=Oswald:wght@500&family=Montserrat:wght@400;500;700&display=swap" rel="stylesheet">
<style>
:root{
  --brand-blue:#5ac2ec;
  --ice-blue:#85cae6;
  --charcoal:#333333;
  --ink:#222222;
  --white:#ffffff;
  --paper:#e9e9e9;
  --icon-grey:#8e9398;
  --backdrop:#4a4a4a;
}
*{margin:0;padding:0;box-sizing:border-box}
html,body{width:1200px;height:1146px;overflow:hidden;background:var(--backdrop)}
.flyer{position:absolute;left:195px;top:0;width:809px;height:1146px;background:var(--paper);overflow:hidden;font-family:'Montserrat',sans-serif}
.hero-photo{position:absolute;left:0;top:0;width:809px;height:303px;background:linear-gradient(180deg,#a9c6dc 0%,#c9d5de 35%,#7b7f86 60%,#5d6168 100%)}
.brand-band{position:absolute;left:0;top:303px;width:809px;height:163px;background:var(--brand-blue)}
.brand-name{position:absolute;left:0;top:28px;width:100%;text-align:center;font-family:'Raleway',sans-serif;font-weight:300;font-size:50px;letter-spacing:0.9em;text-indent:0.9em;color:var(--charcoal)}
.brand-dot{position:absolute;left:398px;top:113px;width:13px;height:13px;border:1.5px solid var(--charcoal);border-radius:50%}
.services-panel{position:absolute;left:0;top:466px;width:809px;height:400px;background:var(--charcoal)}
.tagline-small{position:absolute;top:17px;width:100%;text-align:center;font-family:'Raleway',sans-serif;font-size:11px;letter-spacing:0.35em;color:var(--white)}
.tagline-small::before,.tagline-small::after{content:"";display:inline-block;width:28px;height:1px;background:#777;vertical-align:middle;margin:0 14px}
.tagline-large{position:absolute;top:44px;width:100%;text-align:center;font-family:'Raleway',sans-serif;font-size:21px;letter-spacing:0.5em;text-indent:0.5em;color:var(--white)}
.services-title{position:absolute;left:85px;top:131px;display:flex;align-items:center;gap:10px;font-family:'Montserrat',sans-serif;font-weight:700;font-size:22px;color:var(--brand-blue)}
.services-title .dot{width:14px;height:14px;border:1.5px solid var(--brand-blue);border-radius:50%}
.service{position:absolute;display:flex;align-items:center;gap:14px;font-family:'Oswald',sans-serif;font-size:21px;color:var(--brand-blue);letter-spacing:-0.01em}
.service svg{width:64px;height:64px;flex:none}
.contact-panel{position:absolute;left:0;top:866px;width:809px;height:280px}
.offer-box{position:absolute;left:210px;top:25px;width:376px;height:84px;border:1px dotted #555;text-align:center;font-family:'Raleway',sans-serif;color:var(--brand-blue)}
.offer-title{margin-top:13px;font-size:31px;font-weight:400;line-height:1}
.offer-sub{margin-top:5px;font-size:16px;font-weight:400;line-height:1.1}
.website{position:absolute;left:0;top:125px;width:100%;text-align:center;font-family:'Montserrat',sans-serif;font-weight:700;font-size:24px;line-height:1.2;letter-spacing:0.1em;color:var(--ink)}
.rule{position:absolute;left:90px;width:600px;height:1.5px;background:var(--ink)}
.rule.upper{top:159px}
.rule.lower{top:190px}
.details{position:absolute;left:0;width:100%;text-align:center;color:#111;line-height:1.2}
.details.address{top:166px;font-size:16px}
.details.contact{top:195px;font-size:17.5px;font-weight:500}
.social{position:absolute;left:368px;top:230px;display:flex;gap:4px}
.social span{width:23px;height:23px;border-radius:50%;background:var(--charcoal)}
</style>
</head>
<body>
<main class="flyer">
  <div class="hero-photo" role="img" aria-label="Photo of the technician standing beside the branded service ute at the beach"></div>

  <section class="brand-band">
    <div class="brand-name">BRISKO</div>
    <div class="brand-dot"></div>
  </section>

  <section class="services-panel">
    <div class="tagline-small">COMMERCIAL</div>
    <div class="tagline-large">REFRIGERATION</div>

    <div class="services-title"><span class="dot"></span>SERVICES</div>

    <div class="service" style="left:311px;top:119px">
      <svg viewBox="0 0 64 64"><circle cx="32" cy="32" r="30" fill="var(--icon-grey)" stroke="var(--ice-blue)" stroke-width="2"/><g fill="none" stroke="#fff" stroke-width="1.8"><rect x="28" y="14" width="8" height="26" rx="4"/><circle cx="32" cy="44" r="6"/><path d="M39 20h4M39 25h4M39 30h4"/></g></svg>
      COMMERCIAL REFRIGERATION
    </div>

    <div class="service" style="left:77px;top:201px">
      <svg viewBox="0 0 64 64"><circle cx="32" cy="32" r="30" fill="var(--icon-grey)" stroke="var(--ice-blue)" stroke-width="2"/><g fill="none" stroke="#fff" stroke-width="1.8"><path d="M20 16h24l-3 32H23z"/><rect x="25" y="27" width="7" height="7"/><rect x="32" y="34" width="7" height="7"/></g></svg>
      ICE MAKERS
    </div>
    <div class="service" style="left:311px;top:201px">
      <svg viewBox="0 0 64 64"><circle cx="32" cy="32" r="30" fill="var(--icon-grey)" stroke="var(--ice-blue)" stroke-width="2"/><g fill="none" stroke="#fff" stroke-width="1.8"><path d="M36 14l-8 14M24 30h14v8H24zM34 38v8M30 48h8"/></g></svg>
      BEER SYSTEMS
    </div>
    <div class="service" style="left:550px;top:201px">
      <svg viewBox="0 0 64 64"><circle cx="32" cy="32" r="30" fill="var(--icon-grey)" stroke="var(--ice-blue)" stroke-width="2"/><path d="M36 14L24 34h8l-4 16 12-22h-8z" fill="none" stroke="#fff" stroke-width="1.8"/></svg>
      ELECTRICAL
    </div>

    <div class="service" style="left:77px;top:283px">
      <svg viewBox="0 0 64 64"><circle cx="32" cy="32" r="30" fill="var(--icon-grey)" stroke="var(--ice-blue)" stroke-width="2"/><g fill="none" stroke="#fff" stroke-width="1.8"><path d="M18 46l28-28M18 18l28 28"/><circle cx="46" cy="18" r="3"/><circle cx="18" cy="18" r="3"/></g></svg>
      24HR SERVICE
    </div>
    <div class="service" style="left:311px;top:283px">
      <svg viewBox="0 0 64 64"><circle cx="32" cy="32" r="30" fill="var(--icon-grey)" stroke="var(--ice-blue)" stroke-width="2"/><g fill="none" stroke="#fff" stroke-width="1.8"><path d="M14 20h6l4 18h22l3-12H22"/><circle cx="27" cy="44" r="2.5"/><circle cx="42" cy="44" r="2.5"/></g></svg>
      SALES
    </div>
    <div class="service" style="left:550px;top:283px">
      <svg viewBox="0 0 64 64"><circle cx="32" cy="32" r="30" fill="var(--icon-grey)" stroke="var(--ice-blue)" stroke-width="2"/><g fill="none" stroke="#fff" stroke-width="1.8"><path d="M20 44l4-10 20-20 6 6-20 20z"/><path d="M20 20l24 24M18 24l6-6"/></g></svg>
      INSTALLATION
    </div>
  </section>

  <section class="contact-panel">
    <div class="offer-box">
      <div class="offer-title">DISCOUNT UNTIL JULY</div>
      <div class="offer-sub">PAY ONLY HALF PRICE OF THE SERVICE FEE</div>
    </div>
    <div class="website">WWW.BRISKO-COOLWORKS.COM.AU</div>
    <div class="rule upper"></div>
    <div class="details address">PO BOX 4410 COOGEE NSW 2034 &nbsp;|&nbsp; ABN: 12 345 678 901 &nbsp;|&nbsp; LIC NO: 401275B</div>
    <div class="rule lower"></div>
    <div class="details contact">0400 123 987 &nbsp;|&nbsp; info@brisko-coolworks.com.au</div>
    <div class="social"><span></span><span></span><span></span></div>
  </section>
</main>
</body>
</html>
```